Corvane Automotive Reconditioning Business Card

We need a professional business card that features our logo, a picture of the employee, and a brief list of our services.
I've attached a logo, and will attach photos at a later date.
The four services that need to be listed are Bumper repair and repainting, road rash repair, clear coat scratch repair, and automotive touch-up.
Target Market(s)
30 - 40 year male general managers of automobile dealerships. They are used to seeing every vendor gimmick under the sun. This brochure needs to impress with its simplicity and honesty.
Industry/Entity Type
Automotive
Look and feel

```html
<!DOCTYPE html>
<html lang="en">
<head>
<meta charset="utf-8">
<title>Corvane Automotive Reconditioning – Business Card</title>
<link rel="stylesheet" href="https://fonts.googleapis.com/css2?family=Open+Sans:wght@400;600;700;800&display=swap">
<style>
  :root {
    --page: #d9d7d3;
    --card-white: #ffffff;
    --ink: #2b2b2b;
    --charcoal: #2e2e2e;
    --orange: #e8501c;
    --wood-dark: #4d4a45;
    --wood-mid: #6c6760;
    --wood-light: #827c72;
    --suit-blue: #3c5680;
    --suit-shadow: #233552;
  }
  * { box-sizing: border-box; margin: 0; padding: 0; }
  html, body { width: 1200px; height: 800px; overflow: hidden; }
  body {
    background: var(--page);
    font-family: "Open Sans", Arial, sans-serif;
    color: var(--ink);
    position: relative;
  }
  .card {
    position: absolute;
    top: 250px;
    width: 525px;
    height: 300px;
    border-radius: 22px;
    overflow: hidden;
    box-shadow: 0 6px 18px rgba(0,0,0,0.18);
  }

  /* Front side */
  .card--front { left: 50px; }
  .front__texture {
    position: absolute; inset: 0;
    background: linear-gradient(90deg,
      var(--wood-mid) 0%, var(--wood-dark) 18%, var(--wood-light) 34%,
      var(--wood-dark) 52%, var(--wood-mid) 70%, var(--wood-dark) 86%, var(--wood-mid) 100%);
  }
  .front__brand {
    position: absolute; left: 0; right: 0; top: 84px;
    text-align: center; color: var(--card-white);
    font-weight: 800;
  }
  .front__brand-name { font-size: 44px; letter-spacing: 2px; line-height: 1; }
  .front__brand-tag { font-size: 15px; letter-spacing: 1.5px; margin-top: 8px; }
  .front__services {
    position: absolute; left: 0; right: 0; top: 212px;
    height: 32px;
    padding: 0 12px;
    background: var(--card-white);
    border-bottom: 3px solid var(--orange);
    display: flex; align-items: center; justify-content: center;
    font-size: 9.6px; font-weight: 400; color: var(--ink);
    white-space: nowrap;
  }

  /* Back side */
  .card--back { left: 625px; background: var(--card-white); }
  .back__photo {
    position: absolute; left: 48px; top: 20px; width: 168px; height: 188px;
    background: linear-gradient(180deg, #ffffff 0%, #ffffff 22%, var(--suit-blue) 45%, var(--suit-shadow) 100%);
  }
  .back__band { position: absolute; left: 0; top: 0; width: 525px; height: 300px; }
  .back__name {
    position: absolute; left: 26px; top: 212px;
    color: var(--card-white); font-size: 14px; line-height: 20px; font-weight: 600; letter-spacing: 2px;
  }
  .back__brand {
    position: absolute; left: 258px; top: 40px; width: 250px;
    color: var(--charcoal); font-weight: 800;
  }
  .back__brand-name { font-size: 34px; letter-spacing: 1.5px; line-height: 1; }
  .back__brand-tag { font-size: 11.5px; letter-spacing: 1px; margin-top: 6px; }
  .back__address {
    position: absolute; left: 282px; top: 108px;
    font-size: 12px; line-height: 16px; font-style: normal;
  }
  .back__contacts {
    position: absolute; left: 264px; top: 146px;
    list-style: none; font-size: 12px; line-height: 16px;
  }
  .back__contacts li { display: flex; align-items: center; gap: 7px; }
  .back__contacts svg { width: 11px; height: 11px; flex: none; }
</style>
</head>
<body>

  <section class="card card--front" aria-label="Card front">
    <div class="front__texture" role="img" aria-label="Weathered grey wood plank background"></div>
    <div class="front__brand">
      <div class="front__brand-name">CORVANE</div>
      <div class="front__brand-tag">AUTOMOTIVE RECONDITIONING</div>
    </div>
    <div class="front__services">Bumper repair and repainting | Road rash repair | Clear coat scratch repair | Automotive touch-up</div>
  </section>

  <section class="card card--back" aria-label="Card back">
    <div class="back__photo" role="img" aria-label="Employee portrait in a blue suit"></div>
    <svg class="back__band" viewBox="0 0 525 300" aria-hidden="true">
      <polygon points="0,208 215,208 243,238 505,238 482,264 0,264" fill="var(--charcoal)"/>
      <polyline points="222,214 246,231 525,231" fill="none" stroke="var(--orange)" stroke-width="2"/>
    </svg>
    <div class="back__name">MARCUS HALE</div>

    <div class="back__brand">
      <div class="back__brand-name">CORVANE</div>
      <div class="back__brand-tag">AUTOMOTIVE RECONDITIONING</div>
    </div>

    <address class="back__address">4820 E. Larkin<br>Dr. Scottsdale, AZ 85250</address>

    <ul class="back__contacts">
      <li>
        <svg viewBox="0 0 12 12"><path d="M2 1h3l1 3-2 1a7 7 0 0 0 3 3l1-2 3 1v3c-6 0-9-3-9-9z" fill="var(--orange)"/></svg>
        555-214-0370
      </li>
      <li>
        <svg viewBox="0 0 12 12"><rect x="3" y="0.5" width="6" height="11" rx="1.2" fill="var(--orange)"/><rect x="4" y="2" width="4" height="6" fill="#fff"/></svg>
        555-214-0380
      </li>
      <li>
        <svg viewBox="0 0 12 12"><rect x="0.5" y="2" width="11" height="8" fill="var(--orange)"/><polyline points="1,2.5 6,7 11,2.5" fill="none" stroke="#fff" stroke-width="1"/></svg>
        info@corvaneauto.com
      </li>
      <li>
        <svg viewBox="0 0 12 12"><circle cx="6" cy="6" r="5" fill="none" stroke="var(--orange)" stroke-width="1.3"/><ellipse cx="6" cy="6" rx="2.2" ry="5" fill="none" stroke="var(--orange)" stroke-width="1"/><line x1="1" y1="6" x2="11" y2="6" stroke="var(--orange)" stroke-width="1"/></svg>
        www.corvaneauto.com
      </li>
    </ul>
  </section>

</body>
</html>
```